Screen-Design für Website (Recruiting Agency)
Ich bin wirklich äußerst zufrieden mit der Arbeit und der Zusammenarbeit: tesmaruplin ist auf jeden meiner Wünsche eingegangen und hat mir auch geduldig die verschiedenesten Varianten erarbeitet, wenn ich mir mal die Vorstellungskraft fehlte. Die 5 Sterne sind mehr als verdient. __ I am really extremely satisfied with the work and the cooperation: tesmaruplin has responded to every one of my wishes and has also patiently worked out the most varied of variants for me when I lacked the imagination. The 5 stars are more than deserved.
Zielgruppe
An english version of the briefing can be found at the end
Briefing:
Kurzbeschreibung des Projektes
ich möchte ich mit einer Agentur für Recruiting zum Januar 2021 selbstständig machen und benötige für meine Website noch ein grundlegendes Screen-Design und Bilder, Kollagen und/oder Illustrationen für die verschiednen Textblöcke für zunächst vier Seiten , die die Inhalte transportieren sollen und 'Lust auf das Lesen der Texte' machen.
Ich lasse mich auch von euch Profis gerne beraten, wenn bspw. Überschriften fehlen, Call-to-Action-Elemente (bspw. Kontaktformulare) anders positioniert oder der Footer andere Inhalte enthalten sollte.
Ich benötige
Frühe Entwicklungs-/Konzeptphase als Entscheidungsgrundlage
Ein Screendesign (als PDF, JPG oder via pv.morlint.com-Webansicht) für eine der vier Seiten und die Entwicklung der dazugehörigen Bildelemente.
Am Ende des Prozesses:
- das Screendesign (als PDF, JPG oder via pv.morlint.com-Webansicht)
- Entwicklung der Bildelemente (Bilder, Kollagen oder Ilustrationen) für die verschiedenen Absätze aller vier Seiten
- webfähige Bild-Formate der einzelenen Elemente (Header, Hintergründe, Bilder) fü ride Wordpress-Umsetzung des Designs
Nachtrag 16.11.2020:
Da bereits mehrfach nachgefragt wurde, konkretisiere ich noch einmal den Ablauf (entschuldigt bitte die Verwirrung):
Ich möchte den Aufwand in der Konzeptionsphase für die teilnehmenden Designer so gering wie möglich halten, daher:
Erwarte ichzunächst ein Screendesign für eine einzige Seite . Auf dieser Basis möchte ich eine Entscheidung treffen können. Dieses Screendesign beinhaltet den grundlegenden Aufbau und das grundlegende Design der miren-Seite, die Elemente, Bilder und/oder Illustrationen, die zu dieser konkreten Seite gehören. Eventuell frage ich euch, ob ihr noch das eine oder andere an diesem Entwurf anpassen oder konkretieseren könntet.
Aufgabenstellung
An english version of the project description and goals can be found at the end
Projektbeschreibung und Ziele
Projekthintergrund
Der Vertrieb soll im Januar 2021 starten und dazu benötige ich eine professionelle Website, die die vorgenannten Zielgruppen „emotional“ zum Stöbern einlädt und neugierig auf mehr miren macht. Vertrauen schafft.
Den Dummy der Website (ein Wordpress-Theme (Varlow: https://bramuth.at/themes/varlow-overview/) mit den bereits finalen Texten finden Sie unter https://mi-kobalt.de.
Hier ist nichts „designt“, sondern dient erst einmal lediglich dazu, das Projekt und die Texte der Seiten zu transportieren und festzulegen. Also bitte nicht an den Anordnungen der Textblöcke, Farbwahl oder Schriftgrößen stören - das ist wirklich nur ein Dummy.
Konkret geht es bei diesem Auftrag um folgende vier Seiten:
_Home
_Stellenanzeigen Recruiting
_Performance Recrutiing
_Recruitment Insights
Alle weiteren Seiten (über uns, Blog, Impressum, usw.) sind exemplarisch zwar schon angelegt, werden aber zu einem späteren Zeitpunkt angegangen.
Ziele
An der Unterseite https://mi-kobalt.de/recruitment_insights/ möchte ich gerne dokumentieren, was ich genau benötige.
Die einzelnen Textblöcke der vier Unterseiten sollen durch Bilder, Collagen und/oder Illustrationen unterstützt werden, die Seite „auflockern“ und dem User helfen, schneller den jeweiligen Inhalt und seinen Vorteil zu erfassen (in der Hoffnung, dass er dann auch die dazugehörigen Texte liest).
Inspirierend fand ich bspw. Seiten wie,
https://www.quenvik.com/insights/
https://www.holdenfeld.com/recruiting-software/plexposts/,
https://www.bavorent.com/solutions/programmatic-job-advertising
https://pelzorix.com/
Wichtige Icons bzw. Logos, die mit der Branche und den Schaltkanälen in Verbindung stehen, habe ich Ihnen als PPT-Datei angehängt, falls Sie diese in einem Entwurf ve..

```html
<!DOCTYPE html>
<html lang="de">
<head>
<meta charset="utf-8">
<title>miren advisory – Recruiting</title>
<link href="https://fonts.googleapis.com/css2?family=Fira+Sans:wght@400;500;600&family=Source+Sans+3:wght@300;400&display=swap" rel="stylesheet">
<style>
:root{
  --navy:#22095e;
  --purple:#8b1fa9;
  --ink:#3b1e8a;
  --text:#666;
  --light:#f4f4f4;
  --form:#2e1f7a;
  --footer:#33106e;
  --line:#e2e2e2;
}
*{margin:0;padding:0;box-sizing:border-box}
html,body{width:1200px;height:2666px;overflow:hidden}
body{font-family:"Source Sans 3",sans-serif;color:var(--text);background:#fff}
.page{position:relative;width:1200px;height:2666px;overflow:hidden}
.abs{position:absolute}
.head{font-family:"Fira Sans",sans-serif}

/* top bar */
.topbar{left:0;top:0;width:1200px;height:37px;background:var(--navy);color:#fff;font:500 12px "Fira Sans",sans-serif}
.topbar .mail{left:64px;top:12px;display:flex;gap:10px;align-items:center}
.topbar .phone{right:54px;top:11px;display:flex;gap:10px;align-items:center}

/* nav */
.nav{left:0;top:37px;width:1200px;height:56px;background:#fff;border-bottom:1px solid var(--line)}
.logo{left:63px;top:10px;font:500 27px "Fira Sans",sans-serif;color:var(--navy);letter-spacing:.2px}
.logo span{font-weight:400}
.menu{right:62px;top:12px;display:flex;gap:0;font:500 13px "Fira Sans",sans-serif;color:var(--navy)}
.menu a{color:inherit;text-decoration:none;padding:7px 13px;border-radius:2px}
.menu a.active{background:var(--purple);color:#fff;margin-right:0}

/* hero */
.hero{left:0;top:93px;width:1200px;height:454px;background:linear-gradient(90deg,#f3f3f3,#f7f7f7)}
.hero-art{left:538px;top:0;width:662px;height:454px;background:radial-gradient(ellipse at 60% 55%,#c9c8f7 0%,#dedcfb 45%,rgba(240,240,252,.2) 75%);border-radius:46% 0 0 0}
.hero h1{left:60px;top:148px;font:600 41px/1.07 "Fira Sans",sans-serif;color:var(--navy)}
.hero h1 em{font-style:normal;color:var(--purple)}
.btn{font:500 15px "Fira Sans",sans-serif;color:#fff;display:flex;align-items:center;justify-content:center;border-radius:3px}
.btn.start{left:62px;top:255px;width:131px;height:43px;background:var(--purple)}
.btn.more{left:211px;top:255px;width:131px;height:43px;background:var(--navy)}

/* intro */
.intro{left:150px;top:598px;width:900px;text-align:center;font:300 22.5px/31px "Source Sans 3",sans-serif;color:var(--ink)}
.intro b{font-weight:400;color:var(--navy)}
.rule-full{left:0;width:1200px;height:1px;background:var(--line)}

/* services */
.sec-title{left:0;top:782px;width:1200px;text-align:center;font:500 24px "Fira Sans",sans-serif;color:var(--ink)}
.sec-sub{left:0;top:824px;width:1200px;text-align:center;font:300 14px "Source Sans 3",sans-serif;color:#666}
.svc .label{font:500 14px "Fira Sans",sans-serif;color:#666}
.svc h2{font:500 21.5px "Fira Sans",sans-serif;color:var(--ink);margin:8px 0 12px}
.svc p{font:300 14.5px/22.6px "Source Sans 3",sans-serif;color:#666}
.rule{left:150px;width:901px;height:1px;background:var(--line)}
.art{border-radius:12px}

/* social row */
.social{left:0;top:1880px;width:1200px;height:92px;display:flex;justify-content:center;gap:38px;align-items:center}
.social .net{display:flex;align-items:center;gap:7px;font:500 15px "Fira Sans",sans-serif;color:var(--ink)}
.dot{width:14px;height:14px;border-radius:50%;background:var(--ink)}

/* contact */
.contact{left:0;top:1972px;width:1200px;height:425px;background:#f3f3f3}
.cta{left:120px;top:80px;width:506px;text-align:center}
.cta h3{font:500 22.5px/27px "Fira Sans",sans-serif;color:var(--ink)}
.cta .lead{font:400 14.5px "Source Sans 3",sans-serif;color:#333;margin-top:24px}
.cta .call{font:300 27px "Source Sans 3",sans-serif;color:#333;margin-top:22px;line-height:28px}
.cta .num{font:600 35px "Fira Sans",sans-serif;color:var(--ink);line-height:38px}
.cta .alt{font:400 17px "Source Sans 3",sans-serif;color:#333;margin-top:22px}
.arrow{left:440px;top:2262px}
.form{left:657px;top:2027px;width:393px;height:315px;background:var(--form)}
.avatar{left:601px;top:2033px;width:80px;height:80px;border-radius:50%;background:radial-gradient(circle,#e7e9fb,#b8bde8);border:4px solid #fff;box-shadow:0 2px 8px rgba(0,0,0,.2)}
.field{left:40px;width:313px;background:#fff;border-radius:2px;font:400 15px "Source Sans 3",sans-serif;color:#333;padding:11px 16px}
.send{left:40px;top:250px;width:313px;height:45px;background:var(--purple);color:#fff;font:500 17px "Fira Sans",sans-serif;display:flex;align-items:center;justify-content:center;border-radius:2px}

/* footer */
.footer{left:0;top:2397px;width:1200px;height:269px;background:var(--footer);color:#fff}
.map{left:560px;top:0;width:640px;height:269px;background:radial-gradient(ellipse at 50% 45%,rgba(90,50,150,.55),rgba(51,16,110,0) 70%)}
.footer h4{font:400 15px "Fira Sans",sans-serif;letter-spacing:.3px}
.footer ul{list-style:none;font:400 13px/22.5px "Source Sans 3",sans-serif}
.footer .addr{font:400 13px/16px "Source Sans 3",sans-serif}
.f-icons{left:670px;top:142px;display:flex;gap:18px;align-items:center;font:500 11px "Fira Sans",sans-serif}
.f-rule{left:150px;top:222px;width:900px;height:1px;background:rgba(255,255,255,.15)}
.copy{left:0;top:236px;width:1200px;text-align:center;font:400 13px "Source Sans 3",sans-serif}
</style>
</head>
<body>
<div class="page">

  <div class="abs topbar">
    <div class="abs mail">
      <svg width="18" height="12" viewBox="0 0 18 12"><rect x="0.5" y="0.5" width="17" height="11" fill="none" stroke="#fff"/><path d="M1 1l8 6 8-6" fill="none" stroke="#fff"/></svg>
      kontakt@miren-advisory.de
    </div>
    <div class="abs phone">
      <svg width="14" height="14" viewBox="0 0 24 24"><path fill="#fff" d="M6.6 10.8a15 15 0 006.6 6.6l2.2-2.2a1 1 0 011-.25 11.4 11.4 0 003.6.57 1 1 0 011 1V20a1 1 0 01-1 1A17 17 0 013 4a1 1 0 011-1h3.5a1 1 0 011 1 11.4 11.4 0 00.57 3.6 1 1 0 01-.25 1z"/></svg>
      +49 6123 555 018
    </div>
  </div>

  <header class="abs nav">
    <div class="abs logo">miren <span>advisory</span></div>
    <nav class="abs menu">
      <a class="active" href="#">Home</a>
      <a href="#">Stellenanzeigen Recruiting</a>
      <a href="#">Performance Recruiting</a>
      <a href="#">Recruitment Insights</a>
      <a href="#">Blog</a>
      <a href="#">Kontakt</a>
    </nav>
  </header>

  <section class="abs hero">
    <div class="abs hero-art" role="img" aria-label="Illustration: zwei Personen arbeiten an schwebenden Website-Fenstern mit Medien-Symbolen"></div>
    <h1 class="abs">Die besten Talente gewinnen.<br><em>Stellen besetzen.</em></h1>
    <div class="abs btn start">Jetzt Starten</div>
    <div class="abs btn more">Mehr Erfahren</div>
  </section>

  <p class="abs intro"><b>Online-Recruiting kann frustrierend sein:</b> Entweder erhält man keine oder viel zu viele unpassende <b>Bewerbungen. Und doch gibt es sie:</b> Die Talente, die perfekt zu Ihren offenen Positionen passen. Wir helfen Ihnen, die besten Talente zu erreichen.</p>
  <div class="abs rule-full" style="top:739px"></div>

  <h2 class="abs sec-title">Was wir für sie tun</h2>
  <p class="abs sec-sub">Wenn Erfahrung und Leidenschaft auf Technologie treffen, dann bekommen Sie die Kandidaten, die Sie brauchen.</p>

  <article class="abs svc" style="left:150px;top:910px;width:490px">
    <div class="label">Stellenanzeigen Recruiting</div>
    <h2>„Post &amp; Pray“ war gestern schon out</h2>
    <p>Während Ihre Wettbewerber noch „beten“, erreichen wir bereits die relevanten Kandidaten, die wirklich zu Ihren offenen Stellen passen: Zielgruppenoptimierte Stellenanzeigen auf den nachweisbar relevanten Jobbörsen, Nischen-Stellenbörsen, Netzwerken oder Special Interest-Portalen.</p>
  </article>
  <div class="abs art" style="left:714px;top:864px;width:337px;height:231px;background:linear-gradient(160deg,#eef6f4,#d7ebe6)" role="img" aria-label="Illustration: Team arbeitet an einem Dashboard mit Stellenanzeigen und Diagrammen"></div>
  <div class="abs rule" style="top:1110px"></div>

  <div class="abs art" style="left:119px;top:1157px;width:393px;height:271px;background:linear-gradient(160deg,#f1f3fb,#dfe9f1)" role="img" aria-label="Illustration: Personen analysieren Auswertungen und Insights auf einem großen Dashboard"></div>
  <article class="abs svc" style="left:543px;top:1181px;width:490px">
    <div class="label">Recruiting Insights</div>
    <h2>Cleverer als Ihr Wettbewerb</h2>
    <p>Seien auch Sie cleverer als Ihre Wettbewerber: Unsere Reruitment Insights informieren Sie über Traffic-Trends, Arbeitsmarkt und Wettbewerb. So beurteilen Sie die Empfehlungen transparent  – bvor Sie uns beauftragen. Kostenlos und unverbindlich.</p>
    <p style="margin-top:22px">Damit Sie sich schneller und effizienter die besseren Talente sichern.</p>
  </article>
  <div class="abs rule" style="top:1475px"></div>

  <article class="abs svc" style="left:151px;top:1557px;width:480px">
    <div class="label">Performance Recruiting</div>
    <h2>Die eigentlich unerreichbaren Talente erreichen</h2>
    <p>miren verwandelt Ihre Stellenanzeigen in sich selbst-optimierende Anzeigenkampagnen. Dank unsere KI-gestützten Recruiting Ads und Stellenanzeigen erreichen Sie auch passive Kandidaten. Das gesamte Internet als Jobbörse.: Bis zu 10-mal mehr Kandidaten. Hocheffizient.</p>
  </article>
  <div class="abs art" style="left:652px;top:1521px;width:409px;height:259px;background:linear-gradient(160deg,#f3eefa,#e2d8f1)" role="img" aria-label="Illustration: Personen wählen Kandidatenprofile auf einem Laptop mit Lupe und Megafon aus"></div>

  <div class="abs rule-full" style="top:1879px"></div>
  <div class="abs social">
    <div class="net"><span class="dot"></span>Stellix</div>
    <div class="net"><span class="dot"></span>Kreisla</div>
    <div class="net"><span class="dot"></span>Bildora</div>
    <div class="net"><span class="dot"></span>Zwitscha</div>
    <div class="net"><span class="dot"></span>Netzwerkin</div>
  </div>

  <section class="abs contact">
    <div class="abs cta">
      <h3>Sie wollen miren in Aktion erleben?<br>Mehr, relevante Bewerbungen erhalten?<br>Stellen besetzen? Mit den besten Talenten?</h3>
      <p class="lead">Wir sind für Sie da und freuen uns auf Ihre Herausforderung.</p>
      <p class="call">Rufen Sie uns an unter</p>
      <p class="num">06123 – 555 018</p>
      <p class="alt">oder kontaktieren Sie uns per Formular:</p>
    </div>
  </section>
  <svg class="abs arrow" width="200" height="72" viewBox="0 0 200 72">
    <path d="M6 60 C60 78 140 60 188 10" fill="none" stroke="var(--purple)" stroke-width="5" stroke-linecap="round"/>
    <path d="M162 10 L190 6 L184 34" fill="none" stroke="var(--purple)" stroke-width="5" stroke-linecap="round" stroke-linejoin="round"/>
  </svg>
  <form class="abs form">
    <div class="abs field" style="top:26px;height:45px">Name</div>
    <div class="abs field" style="top:85px;height:44px">E-Mail</div>
    <div class="abs field" style="top:141px;height:97px">Ihre Nachricht an miren*</div>
    <div class="abs send">Jetzt miren Kontaktieren</div>
  </form>
  <div class="abs avatar" role="img" aria-label="Kleine Illustration: Team am Dashboard"></div>

  <footer class="abs footer">
    <div class="abs map" role="img" aria-label="Dezente Weltkarte im Hintergrund"></div>
    <h4 class="abs" style="left:151px;top:34px">Wichtige Links</h4>
    <ul class="abs" style="left:151px;top:69px">
      <li>Recruitment Insights</li><li>Performance Recruiting</li><li>Stellenanzeigen Recruiting</li><li>Blog</li>
    </ul>
    <ul class="abs" style="left:379px;top:69px">
      <li>Datenschutz</li><li>Impressum</li><li>über uns</li><li>Kontakt</li>
    </ul>
    <h4 class="abs" style="left:669px;top:34px">KONTAKT</h4>
    <div class="abs addr" style="left:669px;top:72px">miren advisory UG<br>Lindauer Str. 7b<br>65349 Ortenbach am Rhein</div>
    <div class="abs addr" style="left:838px;top:72px">Telefon +49 6123 555 018<br>E-Mail kontakt@miren-advisory.de</div>
    <div class="abs f-icons">
      <span>Profilo</span><span>Netzwerkin</span>
      <svg width="14" height="10" viewBox="0 0 14 10"><rect width="14" height="10" fill="#fff"/><path d="M0 0l7 5 7-5" fill="none" stroke="var(--footer)" stroke-width="1.2"/></svg>
    </div>
    <div class="abs f-rule"></div>
    <p class="abs copy">Copyright © 2020. All rights reserved.</p>
  </footer>

</div>
</body>
</html>
```